Bespoke Builders Business Card Design

We need a business card for an established builder of high quality bespoke homes in Auckland and Northland. We build and renovate homes collaboratively facilitating effective communication between owners, builders, architects, suppliers and tradespeople. We have never built or renovated a home that leaks or has faults. We only use reliable materials. We have never been sued or had legal action taken against us. We are honest builders of bespoke homes not group mass produced homes. Our niche market is in character homes. We practice sustainability and have built a lot of coastal property. We have been in business for over thirty years . We would like to see natural colors of the environment sand,sea and maybe vegetation . The design should communicate quality, sustainability,fair pricing, open communication and the originality of bespoke building. And the fact that the builder is registered.

Industry/Entity Type

Business

Contact Information for Business Card

Rowan Tellick Builders
Ph. 021583917
18 Kestrel Rd Harwood Bay Auckland 0814
PO Box 927 Mangawhai 0583

```html
<!DOCTYPE html>
<html lang="en">
<head>
<meta charset="utf-8">
<title>Rowan Tellick Builders – Business Card</title>
<link href="https://fonts.googleapis.com/css2?family=Great+Vibes&family=Tinos:wght@400;700&display=swap" rel="stylesheet">
<style>
  :root {
    --backdrop: #e9e6e1;
    --card: #fbfbfb;
    --plum: #5e0f3c;
    --ink: #141414;
    --shadow: rgba(0,0,0,0.18);
  }
  * { margin: 0; padding: 0; box-sizing: border-box; }
  html, body {
    width: 1200px; height: 892px; overflow: hidden;
    background: var(--backdrop);
  }
  .canvas {
    width: 1200px; height: 892px;
    display: flex; flex-direction: column;
    align-items: center; justify-content: center; gap: 36px;
  }
  .card {
    position: relative;
    width: 700px; height: 400px;
    background: var(--card);
    box-shadow: 0 6px 18px var(--shadow);
    overflow: hidden;
  }
  /* Front */
  .card-front .side-band {
    position: absolute; left: 0; top: 0; bottom: 0;
    width: 150px; background: var(--plum);
  }
  .card-front .divider {
    position: absolute; left: 150px; right: 0; top: 196px;
    height: 2px; background: var(--plum);
  }
  .card-front .company-name {
    position: absolute; left: 182px; top: 104px;
    font-family: "Great Vibes", cursive;
    font-size: 58px; color: var(--ink); white-space: nowrap;
  }
  .contact-list {
    position: absolute; left: 182px; top: 228px;
    list-style: none;
    font-family: "Tinos", serif; font-size: 22px; color: var(--ink);
    line-height: 32px;
  }
  .contact-list li { display: flex; align-items: flex-start; gap: 12px; }
  .contact-icon {
    flex: none; width: 18px; height: 18px; margin-top: 7px;
    background: var(--plum); display: flex; align-items: center; justify-content: center;
  }
  /* Back */
  .card-back {
    display: flex; align-items: center; justify-content: center;
  }
  .card-back .company-name {
    font-family: "Tinos", serif; font-weight: 700;
    font-size: 44px; color: var(--ink);
  }
</style>
</head>
<body>
<main class="canvas">
  <section class="card card-front">
    <div class="side-band"></div>
    <h1 class="company-name">Rowan Tellick Builders</h1>
    <div class="divider"></div>
    <ul class="contact-list">
      <li>
        <span class="contact-icon">
          <svg width="12" height="12" viewBox="0 0 12 12" aria-hidden="true">
            <path d="M3 1.5 L4.6 3.8 L3.7 4.8 C4.3 6.1 5.6 7.5 7 8.2 L8 7.2 L10.4 8.8 L9.4 10.5 C5.5 10.2 1.8 6.5 1.4 2.6 Z" fill="#fff"/>
          </svg>
        </span>
        <span>021583917</span>
      </li>
      <li>
        <span class="contact-icon">
          <svg width="12" height="12" viewBox="0 0 12 12" aria-hidden="true">
            <path d="M6 1 C3.8 1 2.4 2.6 2.4 4.5 C2.4 7 6 11 6 11 C6 11 9.6 7 9.6 4.5 C9.6 2.6 8.2 1 6 1 Z" fill="#fff"/>
            <circle cx="6" cy="4.6" r="1.4" fill="#5e0f3c"/>
          </svg>
        </span>
        <span>18 Kestrel Rd Harwood Bay<br>Auckland 0814 PO Box 927 Mangawhai 0583</span>
      </li>
    </ul>
  </section>

  <section class="card card-back">
    <h2 class="company-name">Rowan Tellick Builders</h2>
  </section>
</main>
</body>
</html>
```